U.S. Popcorn company needs business cards

We are a popcorn company that manufactures popcorn and sells it to grocery stores worldwide. Our theme is "Americana" and our logo is U.S. route 66 which is the most famous highway in the U.S.

We would like the design to be simple and to use both sides. On the back side we would like to see just the logo and website. The front would be normal details

Target Market(s)

Wholesalers, grocers and distributors

Industry/Entity Type

Manufacture

Contact Information for Business Card

Business name: Prairie Lantern Popcorn
Phone: +1 555 308 4726
Email: Dale@prairielanternpopcorn.com
website: www.prairielanternpopcorn.com
Tag Line: "POPped with prairie pride"
Name: Dale Whitcombe
Title: Founder/President

Requirements
Must have
• Either this design should be fun or clean and simple. I will let you show me your thougths.
Nice to have
• Anything that ties in the real Hwy Route 66.
• Colors might need to be red, white and blue incorporated.
Should not have
• Not be too busy.

```html
<!DOCTYPE html>
<html lang="en">
<head>
<meta charset="utf-8">
<title>Prairie Lantern Popcorn – Business Cards</title>
<link rel="stylesheet" href="https://fonts.googleapis.com/css2?family=Questrial&family=Open+Sans:ital,wght@0,400;0,700;1,400&display=swap">
<style>
  :root {
    --navy: #102d63;
    --red: #c4201f;
    --white: #ffffff;
    --paper: #f3f3f3;
    --backdrop: #e6e6e6;
    --ink: #1f3a70;
  }
  * { margin: 0; padding: 0; box-sizing: border-box; }
  html, body { width: 1200px; height: 576px; overflow: hidden; }
  body { background: var(--backdrop); position: relative; font-family: "Questrial", sans-serif; }

  .card { position: absolute; border-radius: 6px; overflow: hidden; }

  .card-back { left: 82px; top: 139px; width: 484px; height: 292px; background: var(--navy); }
  .card-back .brand {
    position: absolute; left: 0; right: 0; top: 92px;
    display: flex; align-items: center; justify-content: center; gap: 14px;
    color: var(--white); font-size: 30px; line-height: 1.15;
  }
  .brand-dot { width: 22px; height: 22px; border-radius: 50%; background: var(--red); flex: none; }
  .card-back .website {
    position: absolute; left: 0; right: 0; top: 256px;
    display: flex; align-items: center; justify-content: center; gap: 12px;
    color: var(--white); font-family: "Open Sans", sans-serif; font-weight: 700; font-size: 11px; letter-spacing: .2px;
  }
  .website .rule { width: 48px; height: 1.5px; background: var(--red); }

  .card-front { left: 602px; top: 138px; width: 481px; height: 292px; background: var(--paper); }
  .card-front .brand {
    position: absolute; left: 24px; top: 52px;
    display: flex; align-items: center; gap: 10px;
    color: var(--navy); font-size: 21px; line-height: 1.15;
  }
  .person { position: absolute; right: 20px; top: 144px; text-align: right; font-family: "Open Sans", sans-serif; }
  .person-name { color: var(--red); font-weight: 700; font-size: 16px; }
  .person-title { color: var(--ink); font-style: italic; font-size: 12px; margin-top: 1px; }

  .contact { position: absolute; left: 26px; top: 196px; list-style: none; font-family: "Questrial", sans-serif; font-size: 13px; color: var(--ink); }
  .contact li { display: flex; align-items: center; gap: 10px; height: 18px; }
  .contact svg { width: 11px; height: 11px; flex: none; }
  .contact .web-accent { color: var(--red); }

  .band-red { position: absolute; left: 0; bottom: 0; width: 270px; height: 18px; background: var(--red); }
  .band-blue { position: absolute; right: 0; bottom: 0; width: 244px; height: 34px; background: var(--navy);
    clip-path: polygon(22px 0, 100% 0, 100% 100%, 0 100%); }
  .tagline { position: absolute; right: 20px; bottom: 8px; color: var(--white); font-family: "Questrial", sans-serif; font-size: 13.5px; white-space: nowrap; }
  .tagline b { font-weight: 700; font-family: "Open Sans", sans-serif; }
</style>
</head>
<body>
  <section class="card card-back">
    <div class="brand"><span class="brand-dot"></span><span>Prairie Lantern<br>Popcorn</span></div>
    <div class="website"><span class="rule"></span>www.prairielanternpopcorn.com<span class="rule"></span></div>
  </section>

  <section class="card card-front">
    <div class="brand"><span class="brand-dot"></span><span>Prairie Lantern<br>Popcorn</span></div>

    <div class="person">
      <div class="person-name">Dale Whitcombe</div>
      <div class="person-title">Founder/President</div>
    </div>

    <ul class="contact">
      <li>
        <svg viewBox="0 0 10 10" aria-hidden="true"><path fill="#c4201f" d="M1 3.2C1 2 2 1.5 5 1.5S9 2 9 3.2V4H7V3H3v1H1zM2 5h6l1 3.5H1z"/></svg>
        +1 555 308 4726
      </li>
      <li>
        <svg viewBox="0 0 10 10" aria-hidden="true"><rect x="0.5" y="2" width="9" height="6" fill="#c4201f"/><path d="M0.8 2.3L5 5.6l4.2-3.3" stroke="#fff" stroke-width="0.8" fill="none"/></svg>
        Dale@prairielanternpopcorn.com
      </li>
      <li>
        <svg viewBox="0 0 10 10" aria-hidden="true"><circle cx="5" cy="5" r="4.3" fill="#c4201f"/><path d="M0.8 5h8.4M5 0.8c-2.2 2.4-2.2 6 0 8.4M5 0.8c2.2 2.4 2.2 6 0 8.4" stroke="#fff" stroke-width="0.6" fill="none"/></svg>
        <span><span class="web-accent">prairielanternpopcorn</span>.com</span>
      </li>
    </ul>

    <div class="band-red"></div>
    <div class="band-blue"></div>
    <div class="tagline">"<b>POP</b>ped with prairie pride"</div>
  </section>
</body>
</html>
```